Design letter head and business card

Hello,

you should design a business card and letter paper for Kranichflug Marketing. In German we write this word with K insteat of C.

Company does not have a logo. But in general, we write Kranichflug Marketing in 2 lines.
First line red: KRANICHFLUG
Second line gray: MARKETING

Red (or wine red) and Gray / Black are our favorite colors.

Company slogan: "Fresh Ground Online Marketing".

Company offers SEO, SEM, SEA, AdWords, Conversion Optimization, Online Markting Consulting ...

The website is old, please do not use this as base for your task.

German letter paper sizes:
Viawable Dimensions : 210 x 297 mm
Needed file dimensions: 212 x 299 mm

Informations to include:

Address:
Kranichflug Marketing GmbH
Lindenweg 23
71592 Weinstadt
Germany

Geschäftsführer | CEO: Bernhard Olzner

Phone: +49 (0) 7151 846 27 05

Fax: +49 (0) 7151 846 27 88

Mail: info@kranichflug-beispiel.de

Web: www.kranichflug-beispiel.de

Amtsgericht Suttgart, HRB 537264

Bank: Rosenauer Bank
IBAN: DE827315480900XXXXXXXX
BIC: GENODES1RSQ

Thanks

Bernhard

Target Market(s)

People who likes to win the online marketing game.

Industry/Entity Type

Business

Contact Information for Business Card

Here is the personal text on the card:

Name:
Bernhard Olzner

Title:
Geschäftsführer | CEO

Address:
Kranichflug Marketing GmbH
Lindenweg 23
71592 Weinstadt
Germany

Phone:
+49 (0) 7151 846 27 05

Fax:
+49 (0) 7151 846 27 88

Mail:
olzner@kranichflug-beispiel.de

Web:
www.kranichflug-beispiel.de

Business Card:
Viewable Dimensions: 85 x 55 mm
Needed file dimensions: 87 x 57mm

Font styles to use
Sans Serif

Requirements
Nice to have
• It would be great to see the dynamics of a helicopter.

```html
<!DOCTYPE html>
<html lang="de">
<head>
<meta charset="utf-8">
<title>Kranichflug Marketing – Visitenkarte Vorderseite</title>
<link rel="stylesheet" href="https://fonts.googleapis.com/css2?family=Saira+Condensed:wght@300;600;700&display=swap">
<style>
  :root {
    --card-bg: #e6e6e7;
    --side-band: #a6a7aa;
    --brand-red: #9a1d20;
    --ink-dark: #262626;
    --mark-gray: #8f8f91;
    --text-font: "Saira Condensed", "Arial Narrow", sans-serif;
  }
  * { margin: 0; padding: 0; box-sizing: border-box; }
  html, body {
    width: 667px;
    height: 1200px;
    overflow: hidden;
    background: var(--card-bg);
  }
  .card-front {
    position: relative;
    width: 667px;
    height: 1200px;
    background: var(--card-bg);
    font-family: var(--text-font);
  }
  .side-band {
    position: absolute;
    left: 0;
    top: 0;
    width: 78px;
    height: 100%;
    background: var(--side-band);
  }
  .brand-dot {
    position: absolute;
    left: 245px;
    top: 340px;
    width: 200px;
    height: 200px;
  }
  .brand-block {
    position: absolute;
    left: 30px;
    right: 0;
    top: 600px;
    text-align: center;
  }
  .brand-name {
    font-weight: 700;
    color: var(--ink-dark);
    font-size: 80px;
    line-height: 70px;
    letter-spacing: 1px;
    text-transform: uppercase;
  }
  .brand-name span { display: block; }
  .slogan {
    margin-top: 18px;
    font-weight: 300;
    font-size: 38px;
    line-height: 1;
    color: var(--ink-dark);
  }
  .web-address {
    position: absolute;
    left: 30px;
    right: 0;
    top: 1086px;
    text-align: center;
    font-weight: 600;
    font-size: 38px;
    line-height: 1.2;
    color: var(--brand-red);
    letter-spacing: 0.5px;
  }
</style>
</head>
<body>
  <main class="card-front">
    <div class="side-band"></div>
    <svg class="brand-dot" viewBox="0 0 200 200" aria-hidden="true">
      <circle cx="100" cy="100" r="100" fill="var(--mark-gray)"/>
    </svg>
    <section class="brand-block">
      <h1 class="brand-name"><span>Kranichflug</span><span>Marketing</span></h1>
      <p class="slogan">Fresh Ground Online Marketing</p>
    </section>
    <p class="web-address">www.kranichflug-beispiel.de</p>
  </main>
</body>
</html>
```